CopperWanderer Stretching and Strength

We need a application design for a our first IOS application. the goal of the application is to categorize stretching and strength routines for triathlon.

We would like to see designs that use the color orange.

The design of the application should be compliant with the last version of the IOS Mobile.

For this first design we need the folowing pages:

1- Sign up
2- Log in
3- Home
4- View Exercises
5- Do it
6- Profile

The description of each page is in the attached document.

We need a logo design for the application. The logo should express that mission of the application that is for stretch and strength training for Triathlon.

We will use https://pellavokit.example to develop the application, if you have any experience of the limitation that this technology have it will be a plus.

If you have any question please feel free to contact us.

Reason: We will extend the deadline to be sure that we select the best design from all of you. we will take the final decision next Tuesday.

Target Market(s)

The market for my aplicación is the Running a Triathlon world.

Logo Text

CopperWanderer

Font styles to use
Serif

Colors
f37122
ffffff
dcdcdc

Requirements
Must have
• In some future we will add more features in the menu. We should considere it for the design.
• The designs should include all the screens in the power point.

```html
<!DOCTYPE html>
<html lang="en">
<head>
<meta charset="utf-8">
<title>Profile</title>
<link href="https://fonts.googleapis.com/css2?family=Roboto:wght@400;500&display=swap" rel="stylesheet">
<style>
  :root {
    --orange: #f37122;
    --white: #ffffff;
    --page: #d6e3ef;
    --screen-bg: #eceff2;
    --label: #4a4d52;
    --value: #5a5d62;
    --rule: #e4a784;
  }
  * { box-sizing: border-box; margin: 0; padding: 0; }
  html, body {
    width: 1200px; height: 1200px; overflow: hidden;
    background: var(--page);
    font-family: "Roboto", Arial, sans-serif;
  }
  .stage { position: relative; width: 1200px; height: 1200px; }
  .screen {
    position: absolute; left: 284px; top: 35px;
    width: 550px; height: 982px;
    transform: scale(1.15); transform-origin: 0 0;
    background: var(--screen-bg);
    overflow: hidden;
    box-shadow: 0 10px 30px rgba(60, 80, 110, 0.18);
  }
  .app-header { background: var(--orange); color: var(--white); height: 98px; position: relative; }
  .status-bar {
    height: 40px; display: flex; align-items: center; justify-content: space-between;
    padding: 0 8px; font-size: 15px;
  }
  .status-left, .status-right { display: flex; align-items: center; gap: 6px; }
  .status-time { position: absolute; left: 0; right: 0; text-align: center; top: 11px; font-size: 16px; }
  .nav-bar { height: 58px; display: flex; align-items: center; justify-content: center; position: relative; }
  .nav-title { font-size: 22px; font-weight: 500; letter-spacing: 0.3px; }
  .menu-button { position: absolute; left: 12px; top: 19px; }
  .profile-summary { position: relative; height: 230px; }
  .avatar {
    position: absolute; left: 54px; top: 36px; width: 134px; height: 134px; border-radius: 50%;
    background: radial-gradient(circle at 50% 45%, #b98868 0%, #7a5a3e 45%, #5f7440 75%, #8a9a5a 100%);
  }
  .profile-name { position: absolute; left: 222px; top: 68px; font-size: 26px; font-weight: 500; color: var(--label); }
  .profile-email { position: absolute; left: 222px; top: 111px; font-size: 21px; color: var(--orange); }
  .details { padding: 0 13px; }
  .detail-row {
    display: flex; justify-content: space-between; align-items: center;
    height: 58px; font-size: 21px;
  }
  .detail-label { color: var(--label); font-weight: 500; }
  .detail-value { color: var(--value); }
  .detail-row.editing .detail-value {
    color: var(--orange); width: 298px; text-align: right;
    border-bottom: 1px solid var(--rule); padding-bottom: 6px; margin-top: 12px;
  }
  .caret { display: inline-block; width: 1px; height: 26px; background: var(--rule); vertical-align: -5px; margin-left: 2px; }
  .save-button {
    position: absolute; left: 37px; top: 891px; width: 476px; height: 60px;
    border: none; border-radius: 30px; background: var(--orange); color: var(--white);
    font-family: "Roboto", Arial, sans-serif; font-size: 21px; font-weight: 500;
    box-shadow: 0 3px 6px rgba(0,0,0,0.15);
  }
</style>
</head>
<body>
<div class="stage">
  <div class="screen">
    <header class="app-header">
      <div class="status-bar">
        <div class="status-left">
          <svg width="48" height="10" viewBox="0 0 48 10" aria-hidden="true">
            <circle cx="5" cy="5" r="4" fill="#fff"/><circle cx="14" cy="5" r="4" fill="#fff"/>
            <circle cx="23" cy="5" r="4" fill="#fff"/>
            <circle cx="32" cy="5" r="3.5" fill="none" stroke="#fff"/><circle cx="41" cy="5" r="3.5" fill="none" stroke="#fff"/>
          </svg>
          <span>NOVA</span>
          <svg width="16" height="12" viewBox="0 0 16 12" aria-hidden="true">
            <path d="M1 4a10 10 0 0 1 14 0M3.5 6.5a6.5 6.5 0 0 1 9 0M6 9a3 3 0 0 1 4 0" stroke="#fff" stroke-width="1.6" fill="none"/>
            <circle cx="8" cy="11" r="1" fill="#fff"/>
          </svg>
        </div>
        <div class="status-time">4:21 PM</div>
        <div class="status-right">
          <svg width="10" height="16" viewBox="0 0 10 16" aria-hidden="true">
            <path d="M1 4l8 7-4 3V2l4 3-8 7" stroke="#fff" stroke-width="1.2" fill="none"/>
          </svg>
          <span>100%</span>
          <svg width="36" height="14" viewBox="0 0 36 14" aria-hidden="true">
            <rect x="0.5" y="0.5" width="31" height="13" rx="3" fill="none" stroke="#fff"/>
            <rect x="2.5" y="2.5" width="27" height="9" rx="1.5" fill="#fff"/>
            <rect x="33" y="4.5" width="2" height="5" rx="1" fill="#fff"/>
          </svg>
        </div>
      </div>
      <nav class="nav-bar">
        <svg class="menu-button" width="26" height="18" viewBox="0 0 26 18" aria-label="Menu">
          <rect y="0" width="26" height="2.4" fill="#fff"/><rect y="7.8" width="26" height="2.4" fill="#fff"/><rect y="15.6" width="26" height="2.4" fill="#fff"/>
        </svg>
        <h1 class="nav-title">PROFILE</h1>
      </nav>
    </header>

    <section class="profile-summary">
      <div class="avatar" role="img" aria-label="Profile photo of the user"></div>
      <div class="profile-name">Mara Ellison</div>
      <div class="profile-email">maraellison98@mailbox.example</div>
    </section>

    <section class="details">
      <div class="detail-row editing"><span class="detail-label">Full Name</span><span class="detail-value">Mara<span class="caret"></span></span></div>
      <div class="detail-row"><span class="detail-label">Username</span><span class="detail-value">maraellison98</span></div>
      <div class="detail-row"><span class="detail-label">Age</span><span class="detail-value">25</span></div>
      <div class="detail-row"><span class="detail-label">Gender</span><span class="detail-value">Male</span></div>
      <div class="detail-row"><span class="detail-label">Email Id</span><span class="detail-value">maraellison98@mailbox.example</span></div>
      <div class="detail-row"><span class="detail-label">City</span><span class="detail-value">Berkeley, US</span></div>
      <div class="detail-row"><span class="detail-label">Sports</span><span class="detail-value">Bike and Running</span></div>
    </section>

    <button class="save-button">SAVE</button>
  </div>
</div>
</body>
</html>
```